Namecard Designs+Logo for a High End Automobile Company

We need a new business card for our company called Nordel Motorwerk.

www.nordelmotorwerk.example.sg
Our new website will be up in 2.5 months time.

We sell used and brand new continental cars like Valcrest, KTR, Almira, Dunvale and etc. Currently we are operating from 2 offices in Singapore and United Kingdom.

We want a design which is serious. We are open to colours but try to keep it at a maximum of 3 colours.

We prefer something simple and minimal. We are open to 2 sides printing or even 2 sided namecards. Both UK and Singapore company offices address must be in; either side by side, front and back, or even 2 sided cards.

The logo can be a text logo, emblem, abstract, pictorial or combination.

We are printing with Printlyx.com so please kindly follow the printing guideline.

http://uk.printlyx.example/help/faq/templates-and-guidelines.html

Rich and Car Enthusiasts

Printing

• Our 2 offices; UK and Singapore.

Our slogan which is " The Automobile Specialist"
• Not more than 3 colours

```html
<!DOCTYPE html>
<html lang="en">
<head>
<meta charset="utf-8">
<title>Nordel Motorwerk – Business Card</title>
<link rel="stylesheet" href="https://fonts.googleapis.com/css2?family=Questrial&display=swap">
<style>
  :root {
    --page: #ffffff;
    --card: #222222;
    --band: #505050;
    --ink: #ffffff;
    --ink-soft: #e2e2e2;
    --mark-faint: #2a2a2a;
  }
  * { box-sizing: border-box; margin: 0; padding: 0; }
  html, body {
    width: 1200px; height: 850px; overflow: hidden;
    background: var(--page);
    font-family: "Questrial", "Century Gothic", sans-serif;
    color: var(--ink);
  }
  .canvas { position: relative; width: 1200px; height: 850px; }

  .card {
    position: absolute;
    width: 624px; height: 368px;
    background: var(--card);
    border-radius: 36px;
    overflow: hidden;
  }
  .card--front { left: 281px; top: 45px; }
  .card--back  { left: 285px; top: 439px; }

  .card__band {
    position: absolute; left: 0; right: 0; bottom: 0;
    height: 36px; background: var(--band);
  }

  /* Brand lockup */
  .brand { position: absolute; text-align: center; }
  .brand__mark {
    display: block; margin: 0 auto;
    border: 4px solid var(--ink); border-radius: 50%;
  }
  .brand__name { display: block; white-space: nowrap; line-height: 1; }
  .brand__slogan { display: block; white-space: nowrap; line-height: 1; color: var(--ink-soft); }

  .card--front .brand { left: 0; right: 0; top: 48px; }
  .card--front .brand__mark { width: 150px; height: 150px; }
  .card--front .brand__name { font-size: 44px; margin-top: 42px; }
  .card--front .brand__slogan { font-size: 17px; margin-top: 6px; }

  .card--back .brand { left: 14px; width: 200px; top: 26px; }
  .card--back .brand__mark { width: 92px; height: 92px; border-width: 3px; }
  .card--back .brand__name { font-size: 22px; margin-top: 44px; }
  .card--back .brand__slogan { font-size: 9.5px; margin-top: 3px; }

  .backdrop-mark {
    position: absolute; left: -40px; top: 40px;
    width: 330px; height: 330px; border-radius: 50%;
    border: 26px solid var(--mark-faint);
  }

  /* Contact block */
  .contact { position: absolute; left: 0; top: 0; width: 100%; height: 100%; font-size: 13px; }
  .contact__title { position: absolute; left: 340px; top: 24px; font-size: 21px; }
  .office { position: absolute; display: flex; line-height: 1.3; }
  .office__label { width: 100px; text-align: right; padding-right: 4px; color: var(--ink-soft); }
  .office--sg { left: 293px; top: 71px; }
  .office--uk { left: 293px; top: 127px; }
  .line { position: absolute; left: 366px; display: flex; align-items: center; gap: 14px; }
  .line--phone { top: 198px; }
  .line--mail  { top: 236px; }
  .line svg { width: 18px; height: 14px; }
</style>
</head>
<body>
<div class="canvas">

  <section class="card card--front" aria-label="Card front">
    <div class="brand">
      <span class="brand__mark"></span>
      <span class="brand__name">Nordel Motorwerk</span>
      <span class="brand__slogan">European Automobile Specialist</span>
    </div>
    <div class="card__band"></div>
  </section>

  <section class="card card--back" aria-label="Card back">
    <div class="backdrop-mark"></div>
    <div class="brand">
      <span class="brand__mark"></span>
      <span class="brand__name">Nordel Motorwerk</span>
      <span class="brand__slogan">European Automobile Specialist</span>
    </div>

    <div class="contact">
      <h2 class="contact__title" style="font-weight:400">Nordel Motorwerk</h2>
      <div class="office office--sg">
        <span class="office__label">Singapore:</span>
        <span>8 Harrowmere Road, One Harrowmere<br>Singapore 058317</span>
      </div>
      <div class="office office--uk">
        <span class="office__label">UK:</span>
        <span>27 Kestrel Rise, UK England<br>county</span>
      </div>
      <div class="line line--phone">
        <svg viewBox="0 0 18 14" aria-hidden="true">
          <path d="M1 4 Q9 -1 17 4 L15 6 L12 4.5 L12 3 Q9 2 6 3 L6 4.5 L3 6 Z" fill="#fff"/>
          <rect x="4" y="6.5" width="10" height="7" rx="1.5" fill="#fff"/>
          <circle cx="9" cy="10" r="1.8" fill="#222"/>
        </svg>
        <span>0400 555 218</span>
      </div>
      <div class="line line--mail">
        <svg viewBox="0 0 18 14" aria-hidden="true">
          <rect x="1" y="1.5" width="16" height="11" fill="none" stroke="#fff" stroke-width="1.2"/>
          <polyline points="1,1.5 9,8 17,1.5" fill="none" stroke="#fff" stroke-width="1.2"/>
        </svg>
        <span>NordelMotorwerk@email.example</span>
      </div>
    </div>
    <div class="card__band"></div>
  </section>

</div>
</body>
</html>
```